Kestrel - Transport company looking for a basic but smart design for the sides of our trailers

We have a logo 'Kestrel' which i would like to keep.
We have 2 companies Kestrel Haulage - Maroon signwriting (general freight ) and Kestrel Refrigerated - Blue signwriting (refrigerated freight) that can share the same design.
I'd like to come up with a basic modern design that will incorporate the Kestrel logo, the company name and the website and maybe an image at the front od some sort, a 3D swish or a stripe or something.
The Kestrel Haulage maroon trailers are too busy and I don't like the icicles on the front of the Kestrel Refrigerated blue trailers.

```html
<!DOCTYPE html>
<html lang="en">
<head>
<meta charset="utf-8">
<title>Kestrel Haulage – Trailer Side</title>
<link rel="stylesheet" href="https://fonts.googleapis.com/css2?family=Exo+2:ital,wght@0,800;1,800&display=swap">
<style>
  :root {
    --maroon: #8e1b1e;
    --red-deep: #a3222a;
    --red-mid: #bd2f36;
    --red-light: #d9444c;
    --shadow: #e4e4e4;
    --white: #ffffff;
  }
  html, body {
    margin: 0;
    padding: 0;
    overflow: hidden;
    background: var(--white);
  }
  .trailer-side {
    position: relative;
    width: 1200px;
    height: 249px;
    background: var(--white);
    overflow: hidden;
  }
  .brand-name {
    position: absolute;
    left: 70px;
    top: 62px;
    margin: 0;
    font-family: "Exo 2", sans-serif;
    font-weight: 800;
    font-style: normal;
    font-size: 88px;
    line-height: 1;
    letter-spacing: 1px;
    color: var(--maroon);
    display: flex;
    align-items: center;
    gap: 14px;
  }
  .brand-dot {
    width: 18px;
    height: 18px;
    border-radius: 50%;
    background: var(--maroon);
  }
  .company-name {
    position: absolute;
    left: 422px;
    top: 92px;
    margin: 0;
    font-family: "Exo 2", sans-serif;
    font-weight: 800;
    font-style: italic;
    font-size: 27px;
    line-height: 1;
    letter-spacing: 1px;
    text-transform: uppercase;
    color: var(--maroon);
  }
  .swoosh {
    position: absolute;
    right: 0;
    top: 0;
    width: 1200px;
    height: 249px;
  }
</style>
</head>
<body>
  <div class="trailer-side">
    <svg class="swoosh" viewBox="0 0 1200 249" aria-hidden="true">
      <defs>
        <linearGradient id="fade-shadow" x1="0" x2="1" y1="0" y2="0">
          <stop offset="0" stop-color="#ffffff"/>
          <stop offset="1" stop-color="#d6d6d6"/>
        </linearGradient>
      </defs>
      <polygon points="760,249 1080,0 1200,0 1200,249" fill="url(#fade-shadow)"/>
      <polygon points="850,249 1135,0 1200,0 1200,249" fill="var(--red-deep)"/>
      <polygon points="900,249 960,200 1200,200 1200,249" fill="var(--red-mid)"/>
      <polygon points="985,175 1050,120 1200,120 1200,175" fill="var(--red-mid)"/>
      <polygon points="1050,100 1115,45 1200,45 1200,100" fill="var(--red-light)"/>
      <polygon points="1000,160 1065,105 1110,105 1045,160" fill="var(--red-light)" opacity="0.6"/>
    </svg>

    <h1 class="brand-name"><span class="brand-dot"></span>Kestrel</h1>
    <p class="company-name">Kestrel Haulage</p>
  </div>
</body>
</html>
```